Natural Medicine & Health/Fitness Coaching studio requires web page

Require a innovative web page for a studio that coaches clients to better health, nutrition and fitness. The studio compromises of Clinical Nutritionists, Naturopaths, Rehab Trainers, Personal Trainers and Sport Coaches. Would like to see earthy but bold designs emphasizing nutritional health and athletic performance.
Updates

Design only launched today.

Target Market(s)

All genders from 20's to 60's, as well as families

Industry/Entity Type

Nutritionist

Coding

Coded - Design and coding required

Number of Pages Required

3 page

Colors
abd037
3277b5
fbee3d
fece3e
33b8a4
f04a50

Requirements
Must have
• Online booking system, ability to message
• Home page
• Coaching/Fitness page
• Nutritional Medicine page
• Must be suitable for both Fitness and Nutrition

```html
<!DOCTYPE html>
<html lang="en">
<head>
<meta charset="utf-8">
<title>Greenleaf Vitality Wellness</title>
<link href="https://fonts.googleapis.com/css2?family=PT+Serif:wght@400;700&family=Open+Sans:wght@400;600;700&display=swap" rel="stylesheet">
<style>
:root{
  --green:#8cc63f;
  --green-deep:#6aa62a;
  --yellow:#fece3e;
  --blue:#3277b5;
  --teal:#33b8a4;
  --red:#f04a50;
  --ink:#333333;
  --muted:#777777;
  --grey-bg:#efefef;
  --footer-bg:#e9e9e9;
  --white:#ffffff;
}
*{box-sizing:border-box;margin:0;padding:0}
html,body{width:1200px;height:4252px;overflow:hidden;background:var(--white)}
body{position:relative;font-family:"Open Sans",Arial,sans-serif;color:var(--ink)}
.abs{position:absolute}
.serif{font-family:"PT Serif",Georgia,serif}

/* header */
.site-header{left:0;top:0;width:1200px;height:100px;background:var(--white);z-index:5}
.brand{left:112px;top:14px;font-family:"PT Serif",Georgia,serif;color:var(--green-deep);font-weight:700;font-size:38px;line-height:1}
.brand small{display:block;font-size:15px;font-weight:700;margin-top:4px;letter-spacing:.5px}
.nav{left:530px;top:40px;display:flex;gap:0}
.nav a{font-size:13px;font-weight:600;color:var(--ink);text-decoration:none;padding:8px 14px;letter-spacing:.3px}
.nav a.active{color:var(--green-deep)}

/* hero */
.hero-photo{left:0;top:100px;width:1200px;height:560px;background:linear-gradient(100deg,#c9b79c 0%,#d8c2a6 25%,#a9b58a 55%,#7d9a5a 80%,#5f7f45 100%)}
.hero-title{left:672px;top:205px;color:var(--white);font-size:56px;line-height:1.05}
.hero-sub{left:672px;top:275px;color:var(--white);font-size:36px}
.hero-tag{left:674px;top:325px;color:#fff;font-size:14px}
.btn{display:inline-block;background:var(--yellow);color:var(--white);font-size:12px;font-weight:700;letter-spacing:.5px;text-align:center;border-radius:26px;text-transform:uppercase}
.hero-btn{left:676px;top:410px;width:184px;height:52px;line-height:52px}
.dots{left:556px;top:596px;display:flex;gap:10px}
.dots span{width:14px;height:14px;border-radius:50%;border:2px solid #fff}
.dots span.on{background:#fff}

/* sections */
.section-title{width:1200px;left:0;text-align:center;font-size:46px;color:var(--ink)}
.section-title em{font-style:normal;color:var(--green-deep)}
.leaf{width:40px;height:26px}
.lead{left:200px;width:800px;text-align:center;font-size:14px;line-height:24px;color:var(--muted)}
.btn-center{left:510px;width:180px;height:52px;line-height:52px}

/* what we do */
.wwd-bg{left:0;top:1180px;width:1200px;height:780px;background:var(--grey-bg)}
.card{width:300px;height:300px;border-radius:18px;overflow:hidden;top:1460px}
.card.a{left:114px;border:4px solid var(--green)}
.card.b{left:444px;border:4px solid var(--red)}
.card.c{left:774px;border:4px solid var(--blue)}
.card .ph{width:100%;height:100%}
.card-title{top:1772px;font-size:20px;color:var(--ink)}
.more{top:1808px;font-size:11px;font-weight:700;color:var(--muted);letter-spacing:.5px}
.arrow{width:44px;height:44px;border-radius:50%;background:var(--green);top:1578px}

/* services */
.svc-circle{width:140px;height:140px;border-radius:50%;background:#f4f8ea;top:2200px}
.svc-title{top:2366px;width:300px;text-align:center;font-size:20px;font-weight:700;color:var(--blue)}
.svc-text{top:2406px;width:260px;text-align:center;font-size:13px;line-height:21px;color:var(--muted)}

/* contact */
.contact-photo{left:0;top:2620px;width:1200px;height:720px;background:linear-gradient(90deg,#a8b56c 0%,#cbb465 30%,#e1a64a 55%,#c96a8e 78%,#e46aa0 100%)}
.contact-box{left:360px;top:2764px;width:480px;height:440px;background:var(--green)}
.contact-box h3{color:#fff;font-size:38px;text-align:center;margin-top:36px;font-weight:400}
.field{left:40px;width:400px;height:36px;background:#fff;font-size:12px;color:#666;padding:10px 14px}
.contact-btn{left:510px;top:3178px;width:180px;height:52px;line-height:52px}

/* newsletter */
.news-input{left:296px;top:3640px;width:516px;height:50px;background:#fff;border:1px solid #ddd;font-size:13px;color:#999;padding:15px 16px 0 76px}
.news-icon{left:296px;top:3640px;width:50px;height:50px;background:var(--green)}
.news-btn{left:812px;top:3640px;width:96px;height:50px;line-height:50px;border-radius:0}
.social{top:3730px;width:36px;height:36px;border-radius:50%}

/* footer */
.footer{left:0;top:3860px;width:1200px;height:340px;background:var(--footer-bg)}
.foot-col{top:3940px;width:300px;text-align:center}
.foot-col h4{font-family:"PT Serif",Georgia,serif;font-size:19px;font-weight:700;margin-bottom:22px;letter-spacing:.5px}
.foot-col p{font-size:13px;line-height:22px;color:#555}
.copyright{left:0;top:4200px;width:1200px;height:52px;line-height:52px;text-align:center;font-size:12px;color:#555;background:var(--white)}
</style>
</head>
<body>

<header class="abs site-header">
  <div class="abs brand">Greenleaf Vitality<small>Wellness Studio</small></div>
  <nav class="abs nav">
    <a class="active" href="#">HOME</a><a href="#">ABOUT US</a><a href="#">COACHING</a><a href="#">FITNESS</a><a href="#">NUTRITION</a><a href="#">CONTACT US</a>
  </nav>
</header>

<!-- hero -->
<div class="abs hero-photo" role="img" aria-label="Photo of a fit person measuring their waist in soft natural light"></div>
<div class="abs hero-title serif">Greenleaf</div>
<div class="abs hero-sub serif">Vitality Wellness</div>
<div class="abs hero-tag">Changing Lives Through Nutrition and Exercise</div>
<div class="abs btn hero-btn">Get Started</div>
<div class="abs dots"><span class="on"></span><span></span><span></span></div>
<svg class="abs" style="left:0;top:560px" width="1200" height="120" viewBox="0 0 1200 120" aria-hidden="true">
  <path d="M0 40 C250 110 450 110 700 60 C900 20 1050 30 1200 60 L1200 120 L0 120Z" fill="var(--green)"/>
  <path d="M0 60 C250 125 450 125 700 78 C900 40 1050 48 1200 80 L1200 120 L0 120Z" fill="var(--white)"/>
</svg>

<!-- welcome -->
<svg class="abs leaf" style="left:580px;top:790px" viewBox="0 0 40 26" aria-hidden="true"><path d="M20 26 V6" stroke="var(--green-deep)" stroke-width="2"/><path d="M20 10 C14 0 4 2 2 6 C8 10 14 12 20 10Z M20 10 C26 0 36 2 38 6 C32 10 26 12 20 10Z" fill="var(--green)"/></svg>
<h1 class="abs section-title serif" style="top:818px;font-size:40px">Welcome To <em>Greenleaf Vitality Wellness</em></h1>
<p class="abs lead" style="top:906px">Our studio brings clinical nutrition, naturopathy and coaching together under one roof so every client gets a plan built around real life. We listen first, test carefully and guide you step by step toward lasting energy, strength and balance. Whether you are recovering, training or simply wanting to feel better, our team is ready to help you move forward.</p>
<div class="abs btn btn-center" style="top:1026px">Read More</div>

<!-- what we do -->
<svg class="abs" style="left:0;top:1150px" width="1200" height="80" viewBox="0 0 1200 80" aria-hidden="true"><path d="M0 40 C300 0 500 70 800 40 C1000 20 1100 30 1200 40 L1200 80 L0 80Z" fill="var(--grey-bg)"/></svg>
<div class="abs wwd-bg"></div>
<svg class="abs leaf" style="left:580px;top:1336px" viewBox="0 0 40 26" aria-hidden="true"><path d="M20 26 V6" stroke="var(--green-deep)" stroke-width="2"/><path d="M20 10 C14 0 4 2 2 6 C8 10 14 12 20 10Z M20 10 C26 0 36 2 38 6 C32 10 26 12 20 10Z" fill="var(--green)"/></svg>
<h2 class="abs section-title serif" style="top:1370px">What We Do</h2>

<div class="abs arrow" style="left:34px"><svg width="44" height="44" viewBox="0 0 44 44" aria-hidden="true"><path d="M25 14 L17 22 L25 30" stroke="#fff" stroke-width="3" fill="none"/></svg></div>
<div class="abs arrow" style="left:1122px"><svg width="44" height="44" viewBox="0 0 44 44" aria-hidden="true"><path d="M19 14 L27 22 L19 30" stroke="#fff" stroke-width="3" fill="none"/></svg></div>

<div class="abs card a"><div class="ph" role="img" aria-label="Photo of a clinical nutritionist holding fresh fruit" style="background:linear-gradient(160deg,#e8eef0,#c9d6d8 55%,#8fb56a)"></div></div>
<div class="abs card b"><div class="ph" role="img" aria-label="Photo of a personal trainer coaching a client in the gym" style="background:linear-gradient(160deg,#b9b2ad,#6f6763 60%,#3f3a38)"></div></div>
<div class="abs card c"><div class="ph" role="img" aria-label="Photo of older adults stretching in a rehab class" style="background:linear-gradient(160deg,#c7d4dc,#8fa4b4 55%,#55697a)"></div></div>

<div class="abs card-title serif" style="left:114px">Clinical Nutritionists</div>
<div class="abs card-title serif" style="left:444px">Personal Trainers</div>
<div class="abs card-title serif" style="left:774px">Rehab Trainers</div>
<div class="abs more" style="left:114px">LEARN MORE &#8594;</div>
<div class="abs more" style="left:444px">LEARN MORE &#8594;</div>
<div class="abs more" style="left:774px">LEARN MORE &#8594;</div>

<svg class="abs" style="left:0;top:1860px" width="1200" height="140" viewBox="0 0 1200 140" aria-hidden="true">
  <path d="M0 40 C250 110 500 100 750 60 C950 30 1100 40 1200 70 L1200 140 L0 140Z" fill="var(--green)"/>
  <path d="M0 62 C250 130 500 122 750 82 C950 52 1100 62 1200 92 L1200 140 L0 140Z" fill="var(--white)"/>
</svg>

<!-- services -->
<svg class="abs leaf" style="left:580px;top:2064px" viewBox="0 0 40 26" aria-hidden="true"><path d="M20 26 V6" stroke="var(--green-deep)" stroke-width="2"/><path d="M20 10 C14 0 4 2 2 6 C8 10 14 12 20 10Z M20 10 C26 0 36 2 38 6 C32 10 26 12 20 10Z" fill="var(--green)"/></svg>
<h2 class="abs section-title serif" style="top:2100px">Our Services</h2>

<div class="abs svc-circle" style="left:200px"><svg width="140" height="140" viewBox="0 0 140 140" aria-hidden="true"><circle cx="62" cy="72" r="16" fill="none" stroke="var(--green-deep)" stroke-width="4"/><circle cx="82" cy="66" r="12" fill="var(--green)"/><path d="M84 54 C86 46 92 44 96 44" stroke="var(--green-deep)" stroke-width="3" fill="none"/></svg></div>
<div class="abs svc-circle" style="left:530px"><svg width="140" height="140" viewBox="0 0 140 140" aria-hidden="true"><path d="M70 40 C82 56 86 66 70 78 C54 66 58 56 70 40Z" fill="var(--green)"/><path d="M44 90 H96 L90 100 H50Z" fill="var(--green-deep)"/></svg></div>
<div class="abs svc-circle" style="left:860px"><svg width="140" height="140" viewBox="0 0 140 140" aria-hidden="true"><circle cx="80" cy="44" r="7" fill="var(--green-deep)"/><path d="M76 54 L66 76 L80 86 L74 104 M66 76 L52 92 M72 60 L90 68 M70 62 L54 60" stroke="var(--green-deep)" stroke-width="5" fill="none" stroke-linecap="round"/></svg></div>

<div class="abs svc-title serif" style="left:120px">Diet Plan</div>
<div class="abs svc-title serif" style="left:450px">Therapies</div>
<div class="abs svc-title serif" style="left:780px">Sport Coach</div>
<p class="abs svc-text" style="left:140px">Meal plans shaped around your body, goals and taste, reviewed with you every few weeks.</p>
<p class="abs svc-text" style="left:470px">Natural treatments from our naturopaths to support recovery, digestion, sleep and stress.</p>
<p class="abs svc-text" style="left:800px">Focused sessions that build speed, strength and skill for your chosen sport or event.</p>

<!-- contact -->
<div class="abs contact-photo" role="img" aria-label="Photo of a calm outdoor meadow with a singing bowl and a person in pink seated nearby"></div>
<svg class="abs" style="left:0;top:2600px" width="1200" height="110" viewBox="0 0 1200 110" aria-hidden="true"><path d="M0 0 H1200 V40 C1000 90 800 100 600 70 C400 40 200 30 0 80Z" fill="var(--white)"/></svg>
<div class="abs contact-box">
  <h3 class="serif">Contact Us</h3>
  <div class="abs field" style="top:110px">Name</div>
  <div class="abs field" style="top:158px">Email</div>
  <div class="abs field" style="top:206px">Phone</div>
  <div class="abs field" style="top:254px;height:92px">Message</div>
</div>
<div class="abs btn contact-btn">Send Now</div>
<svg class="abs" style="left:0;top:3250px" width="1200" height="100" viewBox="0 0 1200 100" aria-hidden="true">
  <path d="M0 50 C250 110 500 100 750 60 C950 30 1100 30 1200 50 L1200 100 L0 100Z" fill="var(--green)"/>
  <path d="M0 70 C250 126 500 118 750 80 C950 50 1100 50 1200 70 L1200 100 L0 100Z" fill="var(--white)"/>
</svg>

<!-- newsletter -->
<h2 class="abs section-title serif" style="top:3480px;font-size:42px">Subscribe Our Newsletter</h2>
<p class="abs lead" style="top:3552px;left:330px;width:540px">Get seasonal recipes, training tips and studio news delivered to your inbox each month, with no spam and easy unsubscribe.</p>
<div class="abs news-input">Enter Your Email Address</div>
<div class="abs news-icon"><svg width="50" height="50" viewBox="0 0 50 50" aria-hidden="true"><rect x="14" y="17" width="22" height="16" fill="none" stroke="#fff" stroke-width="2"/><path d="M14 17 L25 26 L36 17" stroke="#fff" stroke-width="2" fill="none"/></svg></div>
<div class="abs btn news-btn">Subscribe</div>
<div class="abs social" style="left:492px;background:var(--blue)"></div>
<div class="abs social" style="left:538px;background:var(--teal)"></div>
<div class="abs social" style="left:584px;background:#f39c12"></div>
<div class="abs social" style="left:630px;background:var(--red)"></div>
<div class="abs social" style="left:676px;background:#2a6fa3"></div>

<!-- footer -->
<footer class="abs footer"></footer>
<div class="abs foot-col" style="left:110px"><h4>ABOUT US</h4><p>A friendly team of nutritionists, naturopaths and trainers helping people of every age live with more energy and ease.</p></div>
<div class="abs foot-col" style="left:450px"><h4>OPEN HOURS</h4><p>Mon-Fri: 6.00am - 8.00pm<br>Saturday: 7.00am - 2.00pm<br>Sunday: Closed</p></div>
<div class="abs foot-col" style="left:790px"><h4>CONTACTS</h4><p>48 Fernbrook Lane, Hollowvale 4021<br>Email: hello@greenleafvitality.example<br>Telephone: (07) 5550 1827</p></div>
<div class="abs copyright">&copy; Copyright Greenleaf Vitality Wellness. All Rights Reserved.</div>

</body>
</html>
```